Andaman Breeze - Rental Villa Website

I have a villa for rent in Thailand and require a website - i need to demo pictures/walk through video, local attractions, villa facilities description plus seaonal rates and online booking.

Industry/Entity Type

Rental

Coding

Coded - Design and coding required

```html
<!DOCTYPE html>
<html lang="en">
<head>
<meta charset="utf-8">
<title>Andaman Breeze Villa – Rental Villa</title>
<link rel="stylesheet" href="https://fonts.googleapis.com/css2?family=Lato:wght@400;700&family=Roboto:wght@400;500&display=swap">
<style>
:root{
  --gold:#8b6b1d;
  --gold-dark:#7a5c14;
  --gold-light:#b99a4e;
  --cream:#f1e9d5;
  --white:#ffffff;
  --grey-bg:#f3f3f3;
  --ink:#2b2b2b;
  --ink-soft:#555555;
}
*{box-sizing:border-box;margin:0;padding:0}
html,body{width:1200px;height:2642px;overflow:hidden}
body{position:relative;background:var(--cream);font-family:"Lato",Arial,sans-serif;color:var(--ink)}
.abs{position:absolute}

/* header */
.lang{left:124px;top:24px;font-size:14px;color:#333}
.account{right:100px;top:24px;display:flex;gap:28px;font-size:14px;color:#333}
.account span{display:flex;align-items:center;gap:7px}
.brand{left:450px;top:34px;width:300px;text-align:center;font-weight:700;font-size:26px;color:var(--gold);line-height:1.15}
.brand .dot{display:inline-block;width:12px;height:12px;border-radius:50%;background:var(--gold);margin-right:8px;vertical-align:middle}
.brand small{display:block;font-size:15px;letter-spacing:3px;margin-top:4px}

.main-nav{left:99px;top:141px;width:1002px;height:46px;background:linear-gradient(#fdfdfd,#eeeeee);display:flex;align-items:center;font-family:"Roboto",Arial,sans-serif;font-size:14px;color:#333}
.main-nav a{flex:1;text-align:center;line-height:46px}
.main-nav a.active{flex:0 0 91px;margin-left:25px;background:linear-gradient(#e9e9e9,#d6d6d6)}

/* hero */
.hero{left:99px;top:189px;width:1002px;height:446px;background:linear-gradient(100deg,#5a3d2c 0%,#c9c2b6 30%,#e2ddd3 55%,#8f8a7c 72%,#c9cbd0 100%)}
.tab{top:394px;height:47px;width:82px;text-align:center;line-height:47px;font-size:17px}
.tab-book{left:206px;background:var(--white);color:#333}
.tab-rent{left:296px;background:var(--gold);color:#fff}
.search{left:206px;top:441px;width:788px;height:99px;background:rgba(139,107,29,.88);border-top:3px solid #fff}
.field{top:471px;height:39px;background:#fff;border-radius:3px;font-size:12px;color:#666;padding:0 10px;display:flex;align-items:center;justify-content:space-between;font-family:"Roboto",Arial,sans-serif}
.btn-book{left:874px;top:471px;width:95px;height:39px;background:#fff;border-radius:3px;font-size:17px;text-align:center;line-height:39px;color:#333;box-shadow:0 3px 0 #333}

/* features */
.feature-icon{width:142px;height:142px;border-radius:50%;background:var(--gold);display:flex;align-items:center;justify-content:center}
.feature-title{font-size:25px;color:var(--gold-dark);text-align:center;width:464px;letter-spacing:.5px}
.feature-text{font-size:12px;line-height:1.4;text-align:justify;color:#222;width:464px}
.btn-gold{background:var(--gold);color:#fff;font-size:13px;border-radius:3px;display:flex;align-items:center;justify-content:center;gap:10px;box-shadow:0 2px 0 #5e4610}

/* about */
.about{left:0;top:1032px;width:1200px;height:315px;background:var(--white)}
.about-title{left:124px;top:1068px;font-size:27px;color:var(--gold-dark)}
.about-text{left:124px;top:1114px;width:464px;font-size:12px;line-height:1.35;text-align:justify;color:#333}
.about-photo{left:612px;top:1122px;width:463px;height:172px;background:linear-gradient(120deg,#6d7a4e 0%,#4d5a63 40%,#8b6f58 70%,#a08a73 100%)}

/* highlights */
.highlights{left:0;top:1347px;width:1200px;height:430px;background:var(--grey-bg)}
.card{top:1465px;width:300px;height:215px;border:1px solid var(--gold-light);background:var(--grey-bg)}
.card-ring{width:114px;height:114px;border-radius:50%;border:1px solid var(--gold-light);background:var(--grey-bg);display:flex;align-items:center;justify-content:center}
.card-ring div{width:102px;height:102px;border-radius:50%;background:var(--gold);display:flex;align-items:center;justify-content:center}
.card-title{width:300px;text-align:center;font-size:16px;color:var(--gold-dark);letter-spacing:.5px}
.card-text{width:260px;font-size:11.5px;line-height:1.4;text-align:justify;text-align-last:center;color:var(--gold-dark);font-weight:700}
.btn-more{width:104px;height:34px;background:var(--gold-dark);color:#fff;font-size:12px;text-align:center;line-height:34px;border-radius:2px}

/* map */
.map{left:0;top:1777px;width:1200px;height:367px;background:linear-gradient(90deg,#a9c8f2 0%,#dfe6cf 22%,#e7e9d8 55%,#cfdcb7 80%,#a9c8f2 100%)}

/* contact strip */
.contact-row{left:0;top:2144px;width:1200px;height:265px;background:var(--white)}
.contact{left:369px;top:2047px;width:462px;height:362px;background:var(--gold)}
.contact h2{position:absolute;top:30px;width:100%;text-align:center;font-family:"Roboto",Arial,sans-serif;font-weight:400;font-size:27px;color:#fff}
.contact p{position:absolute;top:72px;width:100%;text-align:center;font-size:12px;color:#fff}
.input{position:absolute;left:81px;width:300px;border:1px solid #c9ad6a;font-size:11px;color:#f3e8cc;padding:0 16px;font-family:"Roboto",Arial,sans-serif}
.btn-submit{left:542px;top:2389px;width:114px;height:32px;background:#fff;border:1px solid #ccc;border-radius:3px;text-align:center;line-height:30px;font-size:11px;font-weight:700;color:#222;z-index:5}
.foot-brand{left:124px;top:2222px;width:220px;text-align:center;font-weight:700;font-size:22px;color:var(--gold);line-height:1.15}
.foot-brand .dot{display:inline-block;width:10px;height:10px;border-radius:50%;background:var(--gold);margin-right:7px;vertical-align:middle}
.foot-text{left:124px;top:2296px;width:220px;font-size:12px;line-height:1.45;text-align:justify;color:#333}
.gallery-title{left:857px;top:2186px;font-family:"Roboto",Arial,sans-serif;font-size:27px;color:#333}
.thumb{width:67px;height:65px}

/* footer */
.footer-band{left:0;top:2409px;width:1200px;height:76px;background:var(--gold)}
.contact-item{top:2442px;font-size:12px;color:#fff;display:flex;align-items:center;gap:8px}
.social{top:2434px;display:flex;gap:9px;left:976px}
.social span{width:28px;height:28px;border:1px solid #fff;border-radius:2px;display:block}
.skyline{left:0;top:2497px;width:1200px;height:145px;background:linear-gradient(180deg,rgba(190,196,204,0) 0%,#c9ced6 40%,#b3b9c3 100%)}
.copyright{left:0;top:2511px;width:1200px;text-align:center;font-size:12px;color:#444;z-index:2}
</style>
</head>
<body>

<header>
  <div class="abs lang">English &#9662;</div>
  <div class="abs account">
    <span><svg width="12" height="12" viewBox="0 0 12 12"><circle cx="6" cy="6" r="6" fill="#333"/><path d="M6 3v6M3 6h6" stroke="#fff" stroke-width="1.6"/></svg>Register</span>
    <span><svg width="13" height="13" viewBox="0 0 13 13"><circle cx="4" cy="4" r="3" fill="none" stroke="#333" stroke-width="1.5"/><path d="M6 6l6 6M9.5 9.5l-1.5 1.5" stroke="#333" stroke-width="1.5"/></svg>Login</span>
  </div>
  <div class="abs brand"><span class="dot"></span>Andaman Breeze<small>VILLA</small></div>

  <nav class="abs main-nav">
    <a class="active">Home</a><a>About Villa</a><a>Servies</a><a>Gallery</a><a>Reservation</a><a>Blog</a><a>Booking</a><a>Contact Us</a>
  </nav>
</header>

<section>
  <div class="abs hero" role="img" aria-label="Photo of the villa living room with a large painting and bed"></div>
  <div class="abs tab tab-book">Book</div>
  <div class="abs tab tab-rent">Rent</div>
  <div class="abs search"></div>
  <div class="abs field" style="left:238px;width:240px">Where Do You Want To Book?</div>
  <div class="abs field" style="left:487px;width:120px">Arrival <svg width="12" height="12" viewBox="0 0 12 12"><rect x="1" y="2" width="10" height="9" fill="none" stroke="#777"/><path d="M1 5h10M4 1v2M8 1v2" stroke="#777"/></svg></div>
  <div class="abs field" style="left:616px;width:120px">Departure <svg width="12" height="12" viewBox="0 0 12 12"><rect x="1" y="2" width="10" height="9" fill="none" stroke="#777"/><path d="M1 5h10M4 1v2M8 1v2" stroke="#777"/></svg></div>
  <div class="abs field" style="left:745px;width:120px">Person <span>&#8964;</span></div>
  <div class="abs btn-book">Book</div>
</section>

<section>
  <div class="abs feature-icon" style="left:285px;top:681px">
    <svg width="60" height="60" viewBox="0 0 60 60"><path d="M14 14l24-8 10 6v36l-24 8-10-6z" fill="#fff"/><path d="M24 20l18-6M24 27l18-6M24 34l18-6" stroke="#8b6b1d" stroke-width="2"/><path d="M14 14l10 6v36" fill="none" stroke="#8b6b1d" stroke-width="2"/></svg>
  </div>
  <div class="abs feature-title" style="left:124px;top:832px">BOOK A STAY</div>
  <p class="abs feature-text" style="left:124px;top:875px">Lorem ipsum dolor sit amet, consectetur adipisicing elit. Proin nibh augue, suscipit a, scelerisque sed, lacinia in, mi. Cras vel lorem. Etiam pellentesque aliquet tellus. Phasellus pharetra nulla ac diam. Quisque semper justo at risus.Lorem ipsum dolor</p>
  <div class="abs btn-gold" style="left:288px;top:946px;width:136px;height:35px"><svg width="12" height="12" viewBox="0 0 12 12"><path d="M1 0v12" stroke="#fff" stroke-width="1.6"/><path d="M2 1h9l-2 3 2 3H2z" fill="#fff"/></svg>Get Started</div>

  <div class="abs feature-icon" style="left:774px;top:681px">
    <svg width="66" height="50" viewBox="0 0 66 50"><rect x="2" y="6" width="62" height="38" rx="2" fill="#fff"/><rect x="9" y="12" width="48" height="26" fill="none" stroke="#8b6b1d" stroke-width="2"/><circle cx="33" cy="25" r="9" fill="#8b6b1d"/><path d="M33 20v10" stroke="#fff" stroke-width="2.5"/></svg>
  </div>
  <div class="abs feature-title" style="left:612px;top:832px">RENT</div>
  <p class="abs feature-text" style="left:612px;top:875px">Lorem ipsum dolor sit amet, consectetur adipisicing elit. Proin nibh augue, suscipit a, scelerisque sed, lacinia in, mi. Cras vel lorem. Etiam pellentesque aliquet tellus. Phasellus pharetra nulla ac diam. Quisque semper justo at risus.Lorem ipsum dolor</p>
  <div class="abs btn-gold" style="left:776px;top:946px;width:136px;height:35px"><svg width="12" height="12" viewBox="0 0 12 12"><path d="M1 0v12" stroke="#fff" stroke-width="1.6"/><path d="M2 1h9l-2 3 2 3H2z" fill="#fff"/></svg>Get Started</div>
</section>

<section>
  <div class="abs about"></div>
  <h2 class="abs about-title" style="font-weight:400">ABOUT VILLA</h2>
  <p class="abs about-text">Casa was made to make your travelling around the world more exciting and less expensive! Lorem ipsum dolor sit amet, consectetur adipisicing elit. Proin nibh augue, suscipit a, scelerisque sed, lacinia in, mi. Cras vel lorem. Etiam pellentesque aliquet tellus. Phasellus pharetra nulla ac diam. Casa was made to make your travelling around the world more exciting and less expensive! Lorem ipsum dolor sit amet, consectetur adipisicing elit. Proin nibh augue, suscipit a, scelerisque sed, lacinia in, mi. Cras vel lorem. Etiam pellentesque aliquet tellus. Phasellus pharetra nulla ac diam.</p>
  <div class="abs about-photo" role="img" aria-label="Photo of the villa exterior with tiled roof and garden plants"></div>
  <div class="abs btn-gold" style="left:124px;top:1258px;width:137px;height:36px"><svg width="12" height="12" viewBox="0 0 12 12"><path d="M1 0v12" stroke="#fff" stroke-width="1.6"/><path d="M2 1h9l-2 3 2 3H2z" fill="#fff"/></svg>Get Started</div>
</section>

<section>
  <div class="abs highlights"></div>

  <div class="abs card" style="left:124px"></div>
  <div class="abs card-ring" style="left:217px;top:1408px"><div><svg width="44" height="40" viewBox="0 0 44 40"><path d="M22 2L2 20h6v18h10V26h8v12h10V20h6z" fill="#fff"/></svg></div></div>
  <div class="abs card-title" style="left:124px;top:1533px">VILLA DETAILS</div>
  <p class="abs card-text" style="left:144px;top:1565px">Lorem ipsum dolor sit amet, consectetur adipisicing elit, sed do eiusmod tempor incididunt ut labore et dolore magna aliqua. Ut enim ad minim veniam, quis nostrud exercitation ullamco laboris nisi ...</p>
  <div class="abs btn-more" style="left:222px;top:1662px">READ MORE</div>

  <div class="abs card" style="left:450px"></div>
  <div class="abs card-ring" style="left:543px;top:1408px"><div><svg width="48" height="34" viewBox="0 0 48 34"><rect x="1" y="3" width="46" height="28" rx="2" fill="#fff"/><rect x="6" y="8" width="36" height="18" fill="none" stroke="#8b6b1d" stroke-width="2"/><circle cx="24" cy="17" r="6" fill="#8b6b1d"/><path d="M24 14v6" stroke="#fff" stroke-width="2"/></svg></div></div>
  <div class="abs card-title" style="left:450px;top:1533px">MAKING MONEY</div>
  <p class="abs card-text" style="left:470px;top:1565px">Lorem ipsum dolor sit amet, consectetur adipisicing elit, sed do eiusmod tempor incididunt ut labore et dolore magna aliqua. Ut enim ad minim veniam, quis nostrud exercitation ullamco laboris nisi ...</p>
  <div class="abs btn-more" style="left:548px;top:1662px">READ MORE</div>

  <div class="abs card" style="left:776px"></div>
  <div class="abs card-ring" style="left:869px;top:1408px"><div><svg width="46" height="36" viewBox="0 0 46 36"><path d="M3 13a28 28 0 0 1 40 0M9 19a19 19 0 0 1 28 0M15 25a10 10 0 0 1 16 0" fill="none" stroke="#fff" stroke-width="4" stroke-linecap="round"/><circle cx="23" cy="31" r="3.5" fill="#fff"/></svg></div></div>
  <div class="abs card-title" style="left:776px;top:1533px">FREE WIFI</div>
  <p class="abs card-text" style="left:796px;top:1565px">Lorem ipsum dolor sit amet, consectetur adipisicing elit, sed do eiusmod tempor incididunt ut labore et dolore magna aliqua. Ut enim ad minim veniam, quis nostrud exercitation ullamco laboris nisi ...</p>
  <div class="abs btn-more" style="left:874px;top:1662px">READ MORE</div>
</section>

<div class="abs map" role="img" aria-label="Road map of Thailand and neighbouring countries"></div>

<section>
  <div class="abs contact-row"></div>
  <div class="abs foot-brand"><span class="dot"></span>Andaman Breeze<br>Villa</div>
  <p class="abs foot-text">Ut wisi enim ad minim veniam, quis nostrud tation ullamcorper suscipit loborts nisl ut ali ea commodo consequat. Lorem ipsum doloi et, consectetuer adipiscing elitre.</p>

  <div class="abs contact">
    <h2>CONTACT US</h2>
    <p>Aenean commodo ligula egt tash piscing</p>
    <div class="input" style="top:115px;height:44px;line-height:42px">Enter Your Name</div>
    <div class="input" style="top:168px;height:44px;line-height:42px">Enter Your Email</div>
    <div class="input" style="top:221px;height:106px;padding-top:10px">Message</div>
  </div>

  <h2 class="abs gallery-title" style="font-weight:400">Gallery</h2>
  <div class="abs thumb" style="left:857px;top:2238px;background:linear-gradient(#9fb5b8,#5f8d8c)" role="img" aria-label="Pool view"></div>
  <div class="abs thumb" style="left:932px;top:2238px;background:linear-gradient(#6b4a3a,#b5a392)" role="img" aria-label="Villa interior"></div>
  <div class="abs thumb" style="left:1008px;top:2238px;background:linear-gradient(#b9c2c8,#6f8f8a)" role="img" aria-label="Terrace by the pool"></div>
  <div class="abs thumb" style="left:857px;top:2314px;background:linear-gradient(#7f8e8a,#5d8787)" role="img" aria-label="Pool deck"></div>
  <div class="abs thumb" style="left:932px;top:2314px;background:linear-gradient(#5a3b2a,#a6896c)" role="img" aria-label="Covered sala"></div>
  <div class="abs thumb" style="left:1008px;top:2314px;background:linear-gradient(#c5ccd0,#6fa4a4)" role="img" aria-label="Pool and garden"></div>
</section>

<footer>
  <div class="abs footer-band"></div>
  <div class="abs btn-submit">SUBMIT NOW</div>
  <div class="abs contact-item" style="left:124px"><svg width="13" height="13" viewBox="0 0 13 13"><circle cx="6.5" cy="6.5" r="6" fill="#fff"/><path d="M0.5 6.5h12M6.5 0.5c-3 3-3 9 0 12M6.5 0.5c3 3 3 9 0 12" fill="none" stroke="#8b6b1d"/></svg>stay@andamanbreezevilla.example</div>
  <div class="abs contact-item" style="left:395px"><svg width="13" height="13" viewBox="0 0 13 13"><path d="M3 1l2 3-1.5 1.5a7 7 0 0 0 4 4L9 8l3 2-1 2.5C6 13 0 7 0.5 2z" fill="#fff"/></svg>+66 7654 3210</div>
  <div class="abs social"><span></span><span></span><span></span></div>
  <div class="abs skyline" role="img" aria-label="Soft grey city skyline silhouette"></div>
  <div class="abs copyright">© Copyright 2015 &nbsp; | &nbsp; Andaman Breeze &nbsp; | &nbsp; All Rights Reserved</div>
</footer>

</body>
</html>
```